New Fun, Positive, energised looking Business Card Needed for High Achiever Coach

I am looking for a two sided full colour business card. I am self employed and have recently re branded my 1-2-1 work re-vitalising high achievers. My target client base for these cards is therefore high achievers - usually aged 40 -55, they are often entrepreneurs, CEO or work in banking and finance and 2/3 are male. I work with them on 90 day or 6 month coaching programs to help them live their success in a healthier, more sustainable and fulfiiled way. They pay for this privately so though they are corporate types the cards need not look 'corporate'. I want to portray the idea of transformation, vitality and re-connecting.
You can get a feel for the look I like on my new website: morvenlisk.co.uk
I want to use this logo with strapline (Re-Vitalising High Achievers) (I purchased off Logoharbor) and font/ colours (the turquoise and green).
Details to include on the card:
www.morvenlisk.co.uk
+44 7915 302618
morven@morvenlisk.co.uk
skype: morvenlisk
I'd also like to include:
Do you struggle to switch off? Want to be healthier and feel fitter? Want closer relationships? More clarity over the direction you are headed? I can help you do these things using integrated mind-body techniques. Visit morvenlisk.co.uk TODAY to apply for a FREE Breakthrough session.
BUT if that is too much text for a card I am open to advice/ammendments.
Updates
Thanks for your design - I am considering them. PLease change the wording to :

```html
<!DOCTYPE html>
<html lang="en">
<head>
<meta charset="utf-8">
<title>Morven Lisk – Business Card</title>
<link href="https://fonts.googleapis.com/css2?family=Source+Sans+3:wght@400;600;700&display=swap" rel="stylesheet">
<style>
  :root {
    --turquoise: #1ba3cf;
    --green: #63bd6b;
    --white: #ffffff;
    --backdrop: #eef0f1;
    --faint: rgba(255, 255, 255, 0.28);
    --card-w: 540px;
    --card-h: 309px;
  }
  * { box-sizing: border-box; margin: 0; padding: 0; }
  html, body {
    width: 1200px;
    height: 720px;
    overflow: hidden;
    background: var(--backdrop);
    font-family: "Source Sans 3", "Myriad Pro", Arial, sans-serif;
  }
  .canvas {
    width: 1200px;
    height: 720px;
    display: flex;
    align-items: center;
    justify-content: center;
    gap: 40px;
  }
  .card {
    position: relative;
    width: var(--card-w);
    height: var(--card-h);
    overflow: hidden;
    box-shadow: 0 6px 18px rgba(0, 0, 0, 0.12);
  }

  /* Front side */
  .card--front { background: var(--turquoise); }
  .front__brand {
    height: 142px;
    background: var(--white);
    display: flex;
    align-items: center;
    justify-content: center;
    gap: 12px;
  }
  .brand__dot {
    width: 18px;
    height: 18px;
    border-radius: 50%;
    background: var(--green);
  }
  .brand__name {
    font-weight: 700;
    font-size: 40px;
    color: var(--turquoise);
    letter-spacing: 0.5px;
  }
  .contact-list {
    list-style: none;
    position: absolute;
    left: 40px;
    top: 168px;
    color: var(--white);
    font-size: 16px;
    line-height: 27px;
  }
  .contact-list li { display: flex; align-items: center; gap: 9px; }
  .contact-list svg { width: 15px; height: 15px; flex: none; }

  .faint-mark {
    position: absolute;
    font-weight: 700;
    font-size: 30px;
    color: var(--faint);
    white-space: nowrap;
  }
  .card--front .faint-mark { right: 26px; top: 150px; }

  /* Back side */
  .card--back { background: var(--turquoise); color: var(--white); text-align: center; }
  .back__questions {
    height: 168px;
    background: var(--green);
    display: flex;
    flex-direction: column;
    justify-content: center;
    font-size: 18px;
    line-height: 25px;
    padding-top: 8px;
  }
  .back__offer {
    height: 141px;
    display: flex;
    flex-direction: column;
    justify-content: center;
    font-size: 18px;
    line-height: 24px;
  }
  .back__offer p + p { margin-top: 4px; }
  .back__offer strong { font-weight: 700; }
  .card--back .faint-mark { right: 18px; top: 150px; }
</style>
</head>
<body>
<main class="canvas">

  <section class="card card--front" aria-label="Business card front">
    <div class="front__brand">
      <span class="brand__dot"></span>
      <span class="brand__name">Morven Lisk</span>
    </div>
    <span class="faint-mark" aria-hidden="true">Morven Lisk</span>
    <ul class="contact-list">
      <li>
        <svg viewBox="0 0 16 16" aria-hidden="true"><circle cx="8" cy="8" r="7" fill="none" stroke="#fff" stroke-width="1.4"/><path d="M5.5 4.5l1.5 1.5-.8 1a5 5 0 0 0 2.8 2.8l1-.8 1.5 1.5-1 1.2C8 11.5 4.5 8 4.3 5.5z" fill="#fff"/></svg>
        +44 7915 302618
      </li>
      <li>
        <svg viewBox="0 0 16 16" aria-hidden="true"><rect x="1.5" y="3.5" width="13" height="9" rx="1" fill="#fff"/><path d="M2 4l6 5 6-5" fill="none" stroke="#1ba3cf" stroke-width="1.3"/></svg>
        morven@morvenlisk.co.uk
      </li>
      <li>
        <svg viewBox="0 0 16 16" aria-hidden="true"><circle cx="8" cy="8" r="6.5" fill="none" stroke="#fff" stroke-width="1.3"/><ellipse cx="8" cy="8" rx="2.8" ry="6.5" fill="none" stroke="#fff" stroke-width="1.1"/><path d="M1.5 8h13" stroke="#fff" stroke-width="1.1"/></svg>
        www.morvenlisk.co.uk
      </li>
      <li>
        <svg viewBox="0 0 16 16" aria-hidden="true"><circle cx="8" cy="8" r="6.5" fill="#fff"/></svg>
        morvenlisk
      </li>
    </ul>
  </section>

  <section class="card card--back" aria-label="Business card back">
    <div class="back__questions">
      <p>Do you struggle to switch off?</p>
      <p>Want to be healthier and&nbsp; feel fitter?</p>
      <p>Want closer relationships?</p>
      <p>More clarity over the direction you are headed?</p>
    </div>
    <span class="faint-mark" aria-hidden="true">Morven Lisk</span>
    <div class="back__offer">
      <p>I can help you do these things using integrated<br>mind-body techniques.</p>
      <p>Visit <strong>morvenlisk.co.uk</strong> TODAY to apply for a<br>FREE Breakthrough session.</p>
    </div>
  </section>

</main>
</body>
</html>
```